KELBRIDGE PAINTING

We are a painting company. We paint residential, commercial and strata jobs. I need the website to be very sharp, neat and elegant. I've attached our logo. the Logo needs to be embossed as a gold color and the background like a Matt black. I need these tabs:

• HOME • ABOUT US • SERVICES • TESTIMONIALS • SHOWCASE • CONTACT US

Be creative and innovative in your style.
take this as an example to just get the gist of what I'm expecting. If you can better it then the job is yours!

http://rickhalvorpainting.com.au/contact.html

I look forward to seeing your artwork :)

#These are the links to my logo in PSD format.

https://www.filevaultzy.com/s/qwertplk83nd7ha/Kelbridge%20Painting%20Luxury%20Gold.rar

https://www.filevaultzy.com/sh/bzuyrak2m5wqp9/QoPL7-xvMn

Painting

• Making the Logo embossed like the artworks i have attached is definitely a necessity.

Can you let me know if this is possible to apply to the website.

thank you

```html
<!DOCTYPE html>
<html lang="en">
<head>
<meta charset="utf-8">
<title>Kelbridge Painting – Contact us</title>
<link rel="stylesheet" href="https://fonts.googleapis.com/css2?family=Source+Sans+3:ital,wght@0,400;0,600;0,700;1,400&display=swap">
<style>
:root{
  --ink:#1e232b;
  --gold:#f0c04a;
  --gold-deep:#d4a015;
  --gold-mid:#e2b040;
  --gold-soft:#efc676;
  --gold-pale:#f5d9a6;
  --grey-1:#4a4f56;
  --grey-2:#6d7177;
  --grey-3:#9a9ca0;
  --footer:#3f444b;
  --white:#ffffff;
  --rule:#3c424b;
}
*{margin:0;padding:0;box-sizing:border-box}
html,body{width:1040px;height:1200px;overflow:hidden}
body{position:relative;background:var(--ink);font-family:"Source Sans 3",sans-serif;color:var(--white)}
.abs{position:absolute}
.header{left:0;top:0;width:1040px;height:80px;background:var(--ink);border-bottom:1px solid var(--gold-deep);z-index:2}
.header-phone{right:144px;top:16px;font-size:20px;font-weight:700;color:var(--gold);display:flex;align-items:center;gap:8px}
.nav{right:143px;top:55px;display:flex;gap:26px;font-size:12.5px;font-weight:600;letter-spacing:.8px}
.nav a{color:var(--white);text-decoration:none}
.nav a.active{color:var(--gold)}
.hero{left:0;top:80px;width:1040px;height:392px;background:linear-gradient(180deg,#5a4638 0%,#7a5a44 45%,#8a6a58 70%,#b49a8a 100%)}
.brand-badge{left:146px;top:18px;width:100px;height:100px;border-radius:50%;background:var(--ink);border:3px solid var(--gold-deep);z-index:3}
.brand-strip{left:240px;top:80px;width:440px;height:35px;background:linear-gradient(90deg,#e6b945,#f3d373 60%,#e8c050);z-index:3;display:flex;align-items:center;padding-left:14px}
.brand-name{font-size:19px;font-weight:700;letter-spacing:1.4px;color:var(--ink)}
.brand-sep{width:1px;height:16px;background:var(--gold-deep);margin:0 13px}
.brand-tag{font-size:15px;font-style:italic;color:var(--ink)}
.slider-dots{right:144px;top:107px;display:flex;gap:8px;z-index:3}
.slider-dots span{width:8px;height:8px;background:#3a3f46}
.slider-dots span.on{background:var(--gold)}
.caption-accent-left{left:143px;top:290px;width:49px;height:48px;background:var(--gold-mid)}
.caption-accent-right{left:576px;top:340px;width:144px;height:88px;background:var(--gold-mid)}
.caption{left:152px;top:299px;width:552px;height:119px;background:var(--ink);padding:14px 0 0 31px;font-size:37px;line-height:44px;font-weight:400}
.caption-tab{left:674px;top:299px;width:30px;height:6px;background:var(--grey-3)}
.band{left:0;height:8px;width:1040px;display:flex}
.band span{height:100%}
.contact-title{left:143px;top:508px;font-size:38px;font-weight:700;color:var(--gold)}
.intro{left:143px;top:580px;font-size:14.5px}
.field-label{left:143px;font-size:13px;font-weight:400}
.field{left:144px;width:240px;height:32px;background:var(--grey-2)}
.field.focus{background:var(--grey-3);border:1.5px solid var(--gold-deep)}
.field.area{width:368px;height:146px}
.btn{top:1070px;height:32px;display:flex;align-items:center;justify-content:center;font-size:12.5px;font-weight:600;letter-spacing:.5px}
.btn-submit{left:144px;width:76px;background:var(--gold-deep);color:var(--ink);border:1px solid var(--gold-mid)}
.btn-reset{left:232px;width:76px;background:var(--grey-1);color:#c9cbcf}
.details-title{left:679px;top:522px;font-size:24px;font-weight:700;color:var(--gold)}
.details{left:679px;top:561px;width:217px;border-top:1px solid var(--rule)}
.details-row{display:flex;border-bottom:1px solid var(--rule)}
.details-row:last-child{border-bottom:none}
.details-icon{flex:none;width:29px;border-right:1px solid var(--rule);display:flex;justify-content:center;padding-top:12px}
.details-text{max-width:168px;padding:8px 0 8px 13px;font-size:12.5px;line-height:16px}
.details-text.big{max-width:none;font-size:19px;font-weight:600;padding:9px 0 9px 13px;line-height:22px}
.footer{left:0;top:1148px;width:1040px;height:52px;background:var(--footer)}
.copyright{left:145px;top:1166px;font-size:11px}
.social{left:750px;top:1161px;display:flex;gap:14px}
.social span{width:26px;height:26px;border-radius:50%;background:#d4d6d9}
.social span:first-child{background:#3a5ea0}
</style>
</head>
<body>
<header class="abs header">
  <div class="abs header-phone">
    <svg width="18" height="18" viewBox="0 0 24 24"><path fill="#f0c04a" d="M6.6 10.8a15 15 0 0 0 6.6 6.6l2.2-2.2c.3-.3.7-.4 1-.2 1.1.4 2.3.6 3.6.6.6 0 1 .4 1 1V20c0 .6-.4 1-1 1A17 17 0 0 1 3 4c0-.6.4-1 1-1h3.5c.6 0 1 .4 1 1 0 1.3.2 2.5.6 3.6.1.3 0 .7-.2 1z"/></svg>
    1300 47 19 52
  </div>
  <nav class="abs nav">
    <a class="active" href="#">HOME</a><a href="#">ABOUT US</a><a href="#">SERVICES</a><a href="#">TESTIMONIALS</a><a href="#">SHOWCASE</a><a href="#">CONTACT US</a>
  </nav>
</header>

<section class="abs hero" role="img" aria-label="Photo of a modern living room with a brown and cream leather sectional sofa"></section>
<div class="abs brand-badge"></div>
<div class="abs brand-strip"><span class="brand-name">KELBRIDGE PAINTING</span><span class="brand-sep"></span><span class="brand-tag">Colour Done Right, Every Day!</span></div>
<div class="abs slider-dots"><span></span><span></span><span></span><span class="on"></span></div>
<div class="abs caption-accent-left"></div>
<div class="abs caption-accent-right"></div>
<div class="abs caption">We paint residential,<br>commercial and strata jobs</div>
<div class="abs caption-tab"></div>

<div class="abs band" style="top:472px">
  <span style="width:249px"></span>
  <span style="width:71px;background:var(--grey-1)"></span>
  <span style="width:78px;background:var(--grey-2)"></span>
  <span style="width:124px;background:var(--grey-3)"></span>
  <span style="width:104px;background:var(--gold-deep)"></span>
  <span style="width:71px;background:var(--gold-mid)"></span>
  <span style="width:78px;background:var(--gold-soft)"></span>
  <span style="width:265px;background:var(--gold-pale)"></span>
</div>

<h1 class="abs contact-title">Contact us</h1>
<p class="abs intro">For a FREE quote, send us a message:</p>
<div class="abs field-label" style="top:631px">NAME</div>
<div class="abs field focus" style="top:651px"></div>
<div class="abs field-label" style="top:695px">EMAIL</div>
<div class="abs field" style="top:715px"></div>
<div class="abs field-label" style="top:759px">PHONE</div>
<div class="abs field" style="top:779px"></div>
<div class="abs field-label" style="top:823px">ADDRESS</div>
<div class="abs field" style="top:843px"></div>
<div class="abs field-label" style="top:887px">DETAILS</div>
<div class="abs field area" style="top:907px"></div>
<div class="abs btn btn-submit">SUBMIT</div>
<div class="abs btn btn-reset">RESET</div>

<h2 class="abs details-title">Details</h2>
<div class="abs details">
  <div class="details-row">
    <div class="details-icon"><svg width="18" height="18" viewBox="0 0 18 18"><path fill="#8a8e94" d="M8 1h2v16H8zM3 3h11l2 2-2 2H3zM4 8h10v4H4l-2-2z"/></svg></div>
    <div class="details-text">Lorem ipsum dolor sit amet consectetur adipiscing elit Quantum Aristoxeni ingenium consumptum.</div>
  </div>
  <div class="details-row">
    <div class="details-icon"><svg width="16" height="16" viewBox="0 0 24 24"><path fill="#8a8e94" d="M6.6 10.8a15 15 0 0 0 6.6 6.6l2.2-2.2c.3-.3.7-.4 1-.2 1.1.4 2.3.6 3.6.6.6 0 1 .4 1 1V20c0 .6-.4 1-1 1A17 17 0 0 1 3 4c0-.6.4-1 1-1h3.5c.6 0 1 .4 1 1 0 1.3.2 2.5.6 3.6.1.3 0 .7-.2 1z"/></svg></div>
    <div class="details-text big">1300 47 19 52</div>
  </div>
  <div class="details-row">
    <div class="details-icon"><svg width="17" height="12" viewBox="0 0 17 12"><rect x=".5" y=".5" width="16" height="11" fill="none" stroke="#8a8e94"/><path d="M.5.5l8 6 8-6M.5 11.5l6-5M16.5 11.5l-6-5" fill="none" stroke="#8a8e94"/></svg></div>
    <div class="details-text" style="max-width:none">mail@kelbridgepainting.com.au</div>
  </div>
</div>

<div class="abs band" style="top:1140px">
  <span style="width:265px;background:var(--gold-pale)"></span>
  <span style="width:78px;background:var(--gold-soft)"></span>
  <span style="width:71px;background:var(--gold-mid)"></span>
  <span style="width:106px;background:var(--gold-deep)"></span>
  <span style="width:122px;background:var(--grey-3)"></span>
  <span style="width:78px;background:var(--grey-2)"></span>
  <span style="width:71px;background:var(--grey-1)"></span>
</div>
<footer class="abs footer"></footer>
<p class="abs copyright">Copyright @ 2013 Kelbridge Painting. All rights reserved.</p>
<div class="abs social"><span></span><span></span><span></span><span></span></div>
</body>
</html>
```